New Business Card Design

We would like to refresh our business cards and make them look better. We are an IT company specialising in Cloud Services, IT Managed Services, software and hardware. I have attached a PSD of our current design. Also attached our logo.
Updates

I have uploaded all new logos in EPS format.

Can you please edit all designs to include a job title for Marcus Hollis, eg. General Manager

Industry/Entity Type

Software

Colors
ffffff

Requirements
Must have
• Please use white background.
Should not have
• Black background

```html
<!DOCTYPE html>
<html lang="en">
<head>
<meta charset="utf-8">
<title>Corvalis Technology – Business Card</title>
<link rel="stylesheet" href="https://fonts.googleapis.com/css2?family=Open+Sans:wght@400;600;700&display=swap">
<style>
  :root {
    --stage: #e4e6ea;
    --card-white: #ffffff;
    --card-grey: #818a93;
    --brand-red: #bf3425;
    --ink: #2a2a2a;
    --divider: #c9cdd2;
    --rule: #3b3b3b;
  }
  * { box-sizing: border-box; margin: 0; padding: 0; }
  html, body { width: 1200px; height: 987px; overflow: hidden; }
  body {
    background: var(--stage);
    font-family: "Open Sans", Arial, sans-serif;
    position: relative;
  }
  .card {
    position: absolute;
    top: 343px;
    width: 520px;
    height: 300px;
    border-radius: 22px;
    overflow: hidden;
    box-shadow: 0 10px 28px rgba(0,0,0,0.14);
  }
  .card--front { left: 50px; background: var(--card-white); }
  .card--back { left: 630px; background: var(--card-grey); }

  /* front */
  .brand {
    position: absolute;
    left: 30px;
    top: 78px;
    width: 212px;
    display: flex;
    align-items: center;
    gap: 12px;
  }
  .brand__square {
    width: 26px;
    height: 26px;
    background: var(--brand-red);
    flex: none;
  }
  .brand__name {
    font-size: 21px;
    font-weight: 600;
    color: var(--ink);
    line-height: 1.2;
  }
  .card__divider {
    position: absolute;
    left: 258px; top: 48px;
    width: 1px; height: 150px;
    background: linear-gradient(var(--card-white), var(--divider) 25%, var(--divider) 75%, var(--card-white));
  }
  .contact {
    position: absolute;
    left: 282px; top: 52px;
  }
  .contact__name {
    font-size: 21px;
    font-weight: 700;
    color: var(--brand-red);
    line-height: 1.1;
  }
  .contact__role {
    font-size: 14px;
    color: var(--ink);
    margin-bottom: 14px;
  }
  .contact__row {
    display: flex;
    align-items: center;
    gap: 8px;
    font-size: 13.5px;
    color: var(--ink);
    margin-bottom: 6px;
  }
  .contact__row svg { width: 15px; height: 15px; flex: none; }
  .web-band {
    position: absolute;
    left: 0; right: 0; bottom: 34px;
    height: 50px;
    background: var(--brand-red);
    border-top: 4px solid var(--card-white);
    border-bottom: 4px solid var(--card-white);
    box-shadow: 0 -1px 0 var(--rule), 0 1px 0 var(--rule);
    color: var(--card-white);
    font-size: 21px;
    letter-spacing: 1.5px;
    display: flex;
    align-items: center;
    justify-content: center;
  }

  /* back */
  .back__brand {
    position: absolute;
    left: 0; right: 0; top: 88px;
    display: flex;
    justify-content: center;
    align-items: center;
    gap: 12px;
  }
  .back__square {
    width: 26px;
    height: 26px;
    background: var(--card-white);
    flex: none;
  }
  .back__name {
    font-size: 21px;
    font-weight: 600;
    color: var(--card-white);
  }
  .back__text {
    position: absolute;
    left: 0; right: 0; top: 168px;
    text-align: center;
    color: var(--card-white);
  }
  .back__tagline {
    font-size: 16px;
    line-height: 1.35;
  }
  .back__web {
    margin-top: 10px;
    font-size: 12px;
    letter-spacing: 3px;
  }
</style>
</head>
<body>
  <section class="card card--front" aria-label="Business card front">
    <div class="brand">
      <div class="brand__square"></div>
      <div class="brand__name">Corvalis Technology</div>
    </div>
    <div class="card__divider"></div>
    <div class="contact">
      <div class="contact__name">Marcus Hollis</div>
      <div class="contact__role">General Manager</div>
      <div class="contact__row">
        <svg viewBox="0 0 16 16" aria-hidden="true"><circle cx="8" cy="8" r="7.5" fill="#bf3425"/><path d="M5 4.5c.6-.5 1.2-.4 1.5.2l.6 1.2c.2.4 0 .8-.3 1l-.5.4c.5 1 1.3 1.8 2.3 2.3l.4-.5c.3-.3.7-.4 1-.2l1.2.6c.6.3.7.9.2 1.5-.6.7-1.5.9-2.3.5A8 8 0 0 1 4.5 6.8c-.4-.8-.2-1.7.5-2.3z" fill="#fff"/></svg>
        07 3000 4821
      </div>
      <div class="contact__row">
        <svg viewBox="0 0 16 16" aria-hidden="true"><rect x="4" y="1" width="8" height="14" rx="1.5" fill="#bf3425"/><rect x="5.3" y="2.8" width="5.4" height="5" fill="#fff"/><circle cx="6.3" cy="10" r=".7" fill="#fff"/><circle cx="8" cy="10" r=".7" fill="#fff"/><circle cx="9.7" cy="10" r=".7" fill="#fff"/><circle cx="6.3" cy="12" r=".7" fill="#fff"/><circle cx="8" cy="12" r=".7" fill="#fff"/><circle cx="9.7" cy="12" r=".7" fill="#fff"/></svg>
        0400 517 263
      </div>
      <div class="contact__row">
        <svg viewBox="0 0 16 16" aria-hidden="true"><path d="M1 6 8 1.5 15 6v8H1z" fill="#bf3425"/><path d="M3.5 7.5h9L8 10.5z" fill="#fff"/></svg>
        hollism@corvalisit.com.au
      </div>
    </div>
    <div class="web-band">www.corvalisit.com.au</div>
  </section>

  <section class="card card--back" aria-label="Business card back">
    <div class="back__brand">
      <div class="back__square"></div>
      <div class="back__name">Corvalis Technology</div>
    </div>
    <div class="back__text">
      <p class="back__tagline">We are an IT company specializing in Cloud Services<br>IT Managed Services, software and hardware</p>
      <p class="back__web">www.corvalisit.com.au</p>
    </div>
  </section>
</body>
</html>
```